Plakate für ein Fest
Zielgruppe
Das Kessner Park ist ein Gewerbepark mit unterschiedlichen Mietern von Handwerker über Musiker bis hin zu Vermögensberatung. Wir veranstalten ein Fest für unsere Mieter und möchten dieses Plakat als Einladung nutzen.
Aufgabenstellung
Hintergrund schwarz, Logo verwenden
Get together
BBQ & Cocktails im Kessner Park
am 13.10.2023 ab 18 Uhr
Logo Band wild pebbles
Kinderbereich
Wir freuen uns darauf, alle Mieter mit Familien begrüßen zu dürfen! Auch an die Kleinen haben wir gedacht.

```html
<!DOCTYPE html>
<html lang="de">
<head>
<meta charset="utf-8">
<title>BBQ &amp; Cocktails – Kessner Park</title>
<link rel="stylesheet" href="https://fonts.googleapis.com/css2?family=Caveat+Brush&family=Source+Sans+3:wght@300;400;600;700;800&display=swap">
<style>
  :root {
    --bg: #000000;
    --ink: #ffffff;
    --accent: #2ecc63;
    --bun-light: #f3d3a6;
    --bun-mid: #d9924e;
    --sauce: #b4481c;
    --sauce-dark: #5a1c08;
  }
  * { margin: 0; padding: 0; box-sizing: border-box; }
  html, body { width: 848px; height: 1200px; overflow: hidden; background: var(--bg); }
  .poster {
    position: relative;
    width: 848px;
    height: 1200px;
    background: var(--bg);
    color: var(--ink);
    font-family: "Source Sans 3", "Source Sans Pro", sans-serif;
    overflow: hidden;
  }
  .food-photo {
    position: absolute;
    left: 515px;
    top: 88px;
    width: 360px;
    height: 1130px;
    border-radius: 170px 0 0 140px;
    background:
      radial-gradient(ellipse 60% 14% at 70% 7%, var(--bun-light), transparent 70%),
      linear-gradient(180deg,
        var(--bun-mid) 0%, var(--bun-light) 18%, var(--sauce) 30%,
        var(--sauce-dark) 40%, var(--bun-light) 48%, var(--bun-mid) 58%,
        var(--sauce) 70%, var(--sauce-dark) 82%, var(--bun-mid) 94%, var(--bun-light) 100%);
  }
  .kicker {
    position: absolute;
    left: 80px;
    top: 72px;
    font-size: 21px;
    font-weight: 400;
    letter-spacing: 0.2px;
  }
  .kicker strong { color: var(--accent); font-weight: 700; }
  .headline {
    position: absolute;
    left: 60px;
    top: 168px;
    font-family: "Caveat Brush", cursive;
    font-weight: 400;
    font-size: 132px;
    line-height: 1;
    white-space: nowrap;
    transform: rotate(-7deg);
    transform-origin: left bottom;
    z-index: 2;
  }
  .welcome {
    position: absolute;
    left: 75px;
    top: 356px;
    width: 340px;
    font-size: 22.5px;
    font-weight: 300;
    line-height: 37px;
    text-align: justify;
    letter-spacing: 0.6px;
  }
  .welcome strong { font-weight: 700; }
  .date-block {
    position: absolute;
    left: 75px;
    top: 568px;
    padding-left: 23px;
    border-left: 4px solid var(--ink);
    height: 160px;
  }
  .date-block p {
    color: var(--accent);
    font-weight: 600;
    font-size: 100px;
    letter-spacing: -6px;
    line-height: 92px;
    margin-top: -14px;
    white-space: nowrap;
  }
  .info {
    position: absolute;
    left: 75px;
    font-size: 23.5px;
    line-height: 37px;
    font-weight: 300;
  }
  .info .label { color: var(--accent); }
  .info-kids { top: 794px; }
  .info-music { top: 904px; }
  .band-name {
    font-weight: 700;
    font-size: 38px;
    line-height: 44px;
    margin-top: 4px;
    letter-spacing: 0.5px;
  }
  .client-name {
    position: absolute;
    left: 94px;
    top: 1074px;
    display: flex;
    align-items: center;
    gap: 14px;
  }
  .client-name .mark {
    width: 44px;
    height: 44px;
    background: var(--accent);
  }
  .client-name span {
    font-weight: 600;
    font-size: 28px;
    line-height: 26px;
    letter-spacing: 1.5px;
    text-transform: uppercase;
  }
</style>
</head>
<body>
  <main class="poster">
    <div class="food-photo" role="img" aria-label="Foto: gestapelte Burger mit knusprigem, glasiertem Hähnchen, Krautsalat und Gurken, umgeben von Funken"></div>

    <p class="kicker">GET TOGETHER IM <strong>KESSNER PARK</strong></p>

    <h1 class="headline">BBQ &amp; Cocktails</h1>

    <p class="welcome">Wir freuen uns darauf, alle <strong>Mieter mit Familien</strong> begrüßen zu dürfen! Auch an <strong>die Kleinen</strong> haben wir gedacht.</p>

    <div class="date-block">
      <p>13. Oktober<br>18 Uhr</p>
    </div>

    <div class="info info-kids">
      <p class="label">Entertainment für die Kids</p>
      <p>Kinderbereich</p>
    </div>

    <div class="info info-music">
      <p class="label">Musikalische Unterhaltung:</p>
      <p class="band-name">wild pebbles</p>
    </div>

    <div class="client-name">
      <div class="mark"></div>
      <span>Kessner<br>Park</span>
    </div>
  </main>
</body>
</html>
```